OpenHarbor Yoga Website Design

Business Logo - attached
5 pages being:
Home
About
Classes
Blog
Contact

Would like Scrolling webpage and yoga symbols to be used.

Must have's being:
Easy to navigate, Text needs to be able to be edited/updated, Enquire Now Links, More Information Links, be a secure site, SEO,

Please refer to attached document for the information for the body of the website.

Target Market(s)

Educators, Community Service, Health and Wellbeing, Mental Health

Industry/Entity Type

Yoga

Coding

Coded - Design and coding required

Number of Pages Required

5+ page

Font styles to use
Other font styles liked:
• Bella Bold BC

Colors
0094D4
00A9DD
6FCCEA
C7EBF8
E9F6FB
6B429C
8869AF
B7A5CE
E3DAEB
F3F0F8

Requirements
Must have
• Easy to navigate, Text needs to be able to be edited/updated, Enquire Now Links, More Information Links, be a secure site, SEO,
Nice to have
• Scrolling webpage, yoga symbols

```html
<!DOCTYPE html>
<html lang="en">
<head>
<meta charset="utf-8">
<title>OpenHarbor Yoga</title>
<link href="https://fonts.googleapis.com/css2?family=Prata&family=Roboto:wght@400;500;700&display=swap" rel="stylesheet">
<style>
:root{
  --purple:#5b1fd0;
  --purple-light:#8a52f0;
  --cyan:#00a9dd;
  --cyan-dark:#0094d4;
  --ink:#222;
  --text:#444;
  --line:#d9d9d9;
  --white:#fff;
  --lilac:#f3f0f8;
}
*{box-sizing:border-box;margin:0;padding:0}
html,body{width:1200px;height:3279px;overflow:hidden}
body{font-family:"Roboto",Arial,sans-serif;color:var(--text);background:var(--white);position:relative}
.serif{font-family:"Prata",Georgia,serif}
.btn{position:absolute;display:flex;align-items:center;justify-content:center;gap:8px;border-radius:22px;color:var(--white);font-weight:700;font-size:15px;text-transform:uppercase;text-decoration:none}
.btn--cyan{background:var(--cyan)}
.btn--purple{background:var(--purple)}
.btn svg{width:15px;height:15px}

/* header */
.site-header{position:absolute;top:0;left:0;width:1200px;height:90px;background:var(--white);border-top:3px solid var(--cyan);z-index:3}
.brand-badge{position:absolute;left:75px;top:-30px;width:186px;height:186px;border-radius:50%;background:var(--white);display:flex;align-items:flex-end;justify-content:center;padding-bottom:40px}
.brand-badge span{font-family:"Prata",Georgia,serif;font-size:17px;color:var(--purple)}
.main-nav{position:absolute;left:289px;top:34px;display:flex;gap:22px;font-size:15px;color:#333}
.main-nav a{color:#333;text-decoration:none}
.main-nav .active{color:var(--purple);font-weight:700}
.main-nav .sep{color:#555}

/* hero */
.hero{position:absolute;top:90px;left:0;width:1200px;height:652px}
.hero-photo{position:absolute;inset:0;background:linear-gradient(180deg,#5e8a3a 0%,#7fa552 35%,#a7c27a 55%,#6f9a3c 80%,#5a8530 100%)}
.hero-copy{position:absolute;left:110px;top:195px;color:var(--white)}
.hero-copy .kicker{font-size:40px}
.hero-copy h1{font-size:68px;font-weight:400;line-height:1.1;margin-top:4px}
.hero-copy p{font-size:17px;font-weight:700;line-height:26px;width:430px;margin-top:12px}

/* benefits */
.benefits{position:absolute;top:742px;left:0;width:1200px;height:873px}
.section-title{text-align:center;font-size:36px;color:var(--ink);font-weight:400}
.benefits .section-title{position:absolute;top:78px;width:100%}
.benefits .intro{position:absolute;top:135px;width:100%;text-align:center;font-size:15px;line-height:26px;color:#333}
.card{position:absolute;top:223px;width:378px;height:392px;background:var(--white);border-radius:14px;box-shadow:0 4px 22px rgba(0,0,0,.09);padding:26px 40px}
.card h3{font-size:20px;font-weight:500;color:var(--ink);margin-bottom:24px}
.card ul{list-style:none}
.card li{display:flex;align-items:center;gap:13px;font-size:15px;color:#333;line-height:18px;min-height:18px}
.card li svg{flex:none;width:14px;height:14px}
.card--minds{left:200px}
.card--minds li{margin-bottom:18px}
.card--spirits{left:620px;padding-left:50px}
.card--spirits li{margin-bottom:20px}
.slider-arrow{position:absolute;top:403px;width:34px;height:34px;border-radius:50%;background:#f1f1f1;display:flex;align-items:center;justify-content:center}
.slider-arrow svg{width:12px;height:12px}
.benefits .body-copy{position:absolute;width:100%;text-align:center;font-size:15px;line-height:26px;color:#444}

/* welcome */
.welcome{position:absolute;top:1615px;left:0;width:1200px;height:565px;background:linear-gradient(180deg,#8c55f2 0%,#6a2fe0 55%,#5a1fcf 100%)}
.welcome-art{position:absolute;left:110px;top:70px;width:410px;height:420px;border-radius:50%;background:radial-gradient(circle,rgba(255,255,255,.28) 0%,rgba(255,255,255,.08) 60%,rgba(255,255,255,0) 72%)}
.welcome-copy{position:absolute;left:594px;top:62px;width:496px;color:var(--white)}
.welcome-copy h2{font-size:36px;font-weight:400;line-height:42px;margin-bottom:18px}
.welcome-copy p{font-size:15.5px;line-height:25.7px;text-align:justify;margin-bottom:13px}

/* contact */
.contact{position:absolute;top:2180px;left:0;width:1200px;height:570px;background:linear-gradient(180deg,#fafafa,#f4f4f4)}
.contact .section-title{position:absolute;top:78px;width:100%}
.field{position:absolute;height:46px;border:1px solid #cfcfcf;border-radius:23px;background:var(--white);display:flex;align-items:center;gap:12px;padding-left:27px;font-size:13px;color:#333}
.field svg{width:12px;height:12px}
.field--area{height:121px;align-items:flex-start;padding-top:18px}

/* footer */
.site-footer{position:absolute;top:2750px;left:0;width:1200px;height:529px;background:var(--white)}
.footer-brand{position:absolute;left:110px;top:80px;width:195px;text-align:center}
.footer-brand .mark{width:120px;height:120px;border-radius:50%;background:var(--lilac);margin:0 auto 18px}
.footer-brand span{font-family:"Prata",Georgia,serif;font-size:22px;color:var(--purple)}
.abn{position:absolute;left:116px;top:342px;font-size:15px;color:#222}
.footer-col{position:absolute;top:70px}
.footer-col h4{font-size:19px;font-weight:700;color:var(--ink)}
.footer-col h4::after{content:"";display:block;width:26px;height:2px;background:var(--purple);margin-top:10px}
.contact-item{position:absolute;left:0;display:flex;align-items:center;gap:18px;font-size:14px;color:#222;white-space:nowrap}
.contact-item .ico{width:28px;height:28px;border-radius:50%;background:var(--cyan);display:flex;align-items:center;justify-content:center}
.contact-item .ico svg{width:13px;height:13px}
.newsletter p{font-size:14px;line-height:20px;color:#222;margin-top:22px;width:290px}
.subscribe{position:absolute;top:150px;left:0;width:299px;height:44px;border:1px solid #ccc;border-radius:22px;display:flex;align-items:center;padding-left:18px;font-size:12px;color:#555;gap:8px}
.subscribe .btn{right:2px;top:2px;height:38px;width:110px;font-size:12px;position:absolute}
.follow{position:absolute;top:210px;font-size:19px;font-weight:700;color:var(--ink)}
.social{position:absolute;top:262px;width:32px;height:32px;border-radius:50%;background:var(--cyan)}
.footer-rule{position:absolute;left:110px;top:380px;width:978px;height:1px;background:var(--line)}
.footer-nav{position:absolute;top:413px;width:100%;display:flex;justify-content:center;gap:22px;font-size:15px;color:#222}
.copyright{position:absolute;top:465px;width:100%;text-align:center;font-size:13px;color:#222}
</style>
</head>
<body>

<header class="site-header">
  <div class="brand-badge"><span>OpenHarbor Yoga</span></div>
  <nav class="main-nav">
    <a class="active">HOME</a><span class="sep">/</span>
    <a>ABOUT</a><span class="sep">/</span>
    <a>CLASSES</a><span class="sep">/</span>
    <a>BLOG</a><span class="sep">/</span>
    <a>CONTACT</a>
  </nav>
  <a class="btn btn--purple" style="left:784px;top:22px;width:147px;height:40px">Enquire Now</a>
  <a class="btn btn--cyan" style="left:937px;top:22px;width:184px;height:40px">More Information</a>
</header>

<section class="hero">
  <div class="hero-photo" role="img" aria-label="Woman meditating cross-legged on a yoga mat on grass beneath trees"></div>
  <div class="hero-copy">
    <div class="kicker serif">Welcome To</div>
    <h1 class="serif">OpenHarbor Yoga</h1>
    <p>OpenHarbor Yoga believe that you are never too young to benefit from and fall in love with yoga.</p>
  </div>
  <a class="btn btn--cyan" style="left:110px;top:407px;width:168px;height:40px">Get Started
    <svg viewBox="0 0 16 16"><circle cx="8" cy="8" r="8" fill="#fff"/><path d="M5 8h6M8.5 5.5 11 8l-2.5 2.5" stroke="#00a9dd" stroke-width="1.8" fill="none"/></svg></a>
</section>

<svg width="0" height="0" style="position:absolute">
  <symbol id="tick" viewBox="0 0 14 14"><circle cx="7" cy="7" r="7" fill="#00a9dd"/><path d="M4 7.2l2 2 4-4.2" stroke="#fff" stroke-width="1.7" fill="none"/></symbol>
</svg>

<section class="benefits">
  <h2 class="section-title serif">Benefits of Yoga</h2>
  <p class="intro">The benefits of yoga can last a lifetime. It is my aim &amp; passion to introduce yoga to kids of all ages and backgrounds<br>so that they can not only experience the benefits of yoga but fall in love with the practice.</p>

  <div class="slider-arrow" style="left:111px"><svg viewBox="0 0 12 12"><path d="M8 1 3 6l5 5" stroke="#333" stroke-width="1.8" fill="none"/></svg></div>
  <article class="card card--minds">
    <h3>Healthy Minds</h3>
    <ul>
      <li><svg><use href="#tick"/></svg>Cultivates confidence and self-esteem</li>
      <li><svg><use href="#tick"/></svg>Develops concentration and attention</li>
      <li><svg><use href="#tick"/></svg>Clears the mind for better clarity and<br>decision making</li>
      <li><svg><use href="#tick"/></svg>Helps relax and sleep better</li>
      <li><svg><use href="#tick"/></svg>Calms the nervous system</li>
      <li><svg><use href="#tick"/></svg>Learns to cope with stressful situations</li>
      <li><svg><use href="#tick"/></svg>Balances emotions</li>
    </ul>
  </article>
  <article class="card card--spirits">
    <h3>Healthy Spirits</h3>
    <ul>
      <li><svg><use href="#tick"/></svg>Fosters creativity, expression and<br>imagination</li>
      <li><svg><use href="#tick"/></svg>Cultivates kindness to themselves<br>and others</li>
      <li><svg><use href="#tick"/></svg>Cultivates respect for self and others</li>
      <li><svg><use href="#tick"/></svg>Builds balance and inner quiet</li>
      <li><svg><use href="#tick"/></svg>Builds inner strength and resilience</li>
      <li><svg><use href="#tick"/></svg>Teaches self-awareness</li>
      <li><svg><use href="#tick"/></svg>Focuses on positive self-talk</li>
    </ul>
  </article>
  <div class="slider-arrow" style="left:1051px"><svg viewBox="0 0 12 12"><path d="M4 1l5 5-5 5" stroke="#333" stroke-width="1.8" fill="none"/></svg></div>

  <p class="body-copy" style="top:664px">OpenHarbor Yoga combines all the benefits of traditional yoga and a lot of fun!&nbsp; We play games and practice engaging flows which<br>get our bodies moving, then we take a quiet moment to be still and calm as we focus on our breathing.</p>
  <p class="body-copy" style="top:741px">OpenHarbor Yoga Kids will learn that relaxation is just as important as moving their bodies, and the exercises which they learn in<br>class can easily be repeated at any time in their busy day to feel calm and grounded.</p>
</section>

<section class="welcome">
  <div class="welcome-art" role="img" aria-label="Large decorative yoga emblem filled with a misty meadow scene"></div>
  <div class="welcome-copy">
    <h2 class="serif">Welcome to<br>OpenHarbor Yoga</h2>
    <p>OpenHarbor Yoga believe that you are never too young to benefit from and fall in love with yoga. My aim is to EMPOWER kids and teens to thrive by teaching life skills in Yoga, Mindfulness and Breathing techniques to deal with daily challenges and big emotions</p>
    <p>OpenHarbor Yoga gives kids an opportunity to enjoy and experience yoga for themselves and primarily focuses on programs for Schools, Pre Schools and Early Learning Centres, Private Classes, Sporting Clubs, Martial Arts Schools, Scout Groups and Occupational Therapy Centres just to name a few. All classes are age appropriate and encourage children's natural drive to learn, move, and be creative.</p>
  </div>
  <a class="btn btn--cyan" style="left:594px;top:455px;width:167px;height:40px">Learn More
    <svg viewBox="0 0 16 16"><circle cx="8" cy="8" r="8" fill="#fff"/><path d="M5 8h6M8.5 5.5 11 8l-2.5 2.5" stroke="#00a9dd" stroke-width="1.8" fill="none"/></svg></a>
</section>

<section class="contact">
  <h2 class="section-title serif">Contact Us</h2>
  <div class="field" style="left:158px;top:153px;width:438px"><svg viewBox="0 0 12 12"><circle cx="6" cy="3.5" r="3" fill="#222"/><path d="M1 12c0-4 10-4 10 0z" fill="#222"/></svg>First Name</div>
  <div class="field" style="left:604px;top:153px;width:439px"><svg viewBox="0 0 12 12"><circle cx="6" cy="3.5" r="3" fill="#222"/><path d="M1 12c0-4 10-4 10 0z" fill="#222"/></svg>Last Name</div>
  <div class="field" style="left:158px;top:216px;width:438px"><svg viewBox="0 0 12 12"><rect x="0" y="2" width="12" height="8" fill="#222"/><path d="M0 2l6 4 6-4" stroke="#fff" fill="none"/></svg>Email</div>
  <div class="field" style="left:604px;top:216px;width:439px"><svg viewBox="0 0 12 12"><rect x="3" y="0" width="6" height="12" rx="1" fill="#222"/><rect x="4" y="1.5" width="4" height="8" fill="#fff"/></svg>Phone</div>
  <div class="field field--area" style="left:158px;top:278px;width:885px;border-radius:22px"><svg viewBox="0 0 12 12"><ellipse cx="5" cy="5" rx="5" ry="3.5" fill="#222"/><ellipse cx="8" cy="7.5" rx="4" ry="3" fill="#222"/></svg>Comments</div>
  <a class="btn btn--cyan" style="left:516px;top:446px;width:168px;height:39px">Submit Now
    <svg viewBox="0 0 16 16"><circle cx="8" cy="8" r="8" fill="#fff"/><path d="M5 8h6M8.5 5.5 11 8l-2.5 2.5" stroke="#00a9dd" stroke-width="1.8" fill="none"/></svg></a>
</section>

<footer class="site-footer">
  <div class="footer-brand"><div class="mark"></div><span>OpenHarbor Yoga</span></div>
  <div class="abn">ABN:&nbsp; 48 210 975 316</div>

  <div class="footer-col" style="left:418px;width:300px;height:300px">
    <h4>Address</h4>
    <div class="contact-item" style="top:74px;font-weight:700;line-height:22px">
      <span class="ico"><svg viewBox="0 0 12 12"><path d="M6 0a4 4 0 0 0-4 4c0 3 4 8 4 8s4-5 4-8a4 4 0 0 0-4-4z" fill="#fff"/><circle cx="6" cy="4" r="1.5" fill="#00a9dd"/></svg></span>
      <span>Fernvale, Victoria<br>Australia 3990</span></div>
    <div class="contact-item" style="top:148px;font-size:19px;font-weight:700">
      <span class="ico"><svg viewBox="0 0 12 12"><path d="M2.5 0.5 4.5 3 3.3 4.5c.8 1.8 2.2 3.2 4.2 4.2L9 7.5l2.5 2-1.2 2C5 11.5.5 7 .5 1.7z" fill="#fff"/></svg></span>
      <span>0400 518 236</span></div>
    <div class="contact-item" style="top:210px">
      <span class="ico"><svg viewBox="0 0 12 12"><rect x="0" y="2" width="12" height="8" fill="#fff"/><path d="M0 2l6 4 6-4" stroke="#00a9dd" fill="none"/></svg></span>
      <span>&nbsp;info@openharboryoga.com.au</span></div>
    <div class="contact-item" style="top:262px">
      <span class="ico"><svg viewBox="0 0 12 12"><circle cx="6" cy="6" r="5.2" stroke="#fff" fill="none"/><ellipse cx="6" cy="6" rx="2.2" ry="5.2" stroke="#fff" fill="none"/><path d="M1 6h10" stroke="#fff"/></svg></span>
      <span>www.openharboryoga.com.au</span></div>
  </div>

  <div class="footer-col newsletter" style="left:785px;width:310px;height:310px">
    <h4>Subscribe Newsletter</h4>
    <p>Lorem ipsum dolor sit amet, consectetur adipiscing elit, sed do eiusmod</p>
    <div class="subscribe"><svg width="12" height="10" viewBox="0 0 12 10"><rect y="1" width="12" height="8" fill="#555"/><path d="M0 1l6 4 6-4" stroke="#fff" fill="none"/></svg>Email Address *<a class="btn btn--cyan">Subscribe</a></div>
    <div class="follow">Follow Us On</div>
    <span class="social" style="left:2px"></span>
    <span class="social" style="left:43px"></span>
  </div>

  <div class="footer-rule"></div>
  <nav class="footer-nav"><span>HOME</span><span>/</span><span>ABOUT</span><span>/</span><span>CLASSES</span><span>/</span><span>BLOG</span><span>/</span><span>CONTACT</span></nav>
  <div class="copyright">Copyright 2023 OpenHarbor Yoga</div>
</footer>

</body>
</html>
```